Layout für Broschüre für chemiefreie Lösung, Kühlwasser aufzubereiten
Zielgruppe
FLUVITEK hat eine Technologie entwickelt, die in der Industrie eingesetzt wird um in geschlossenen und offenen Kühlkreisläufen ohne Biozide und Korrosion Inhibitoren das Kühlwasser aufzubereiten. Mit FLUVITEK haben die Unternehmen eine chemiefreie Lösungen gegen Biofouling, Korrosion und Kalk. Zielgruppe sind alle Unternehmen die etwas produzieren oder Klimaanlagen / Heizungssysteme betreiben. Es geht um zukunftsorientierte und vor allem nachhaltige Technologie ohne Einsatz von Chemie.
Aufgabenstellung
Wir suchen für die Broschüre ein neues Layout, dass geradlinig und klar strukturiert ist, vor allem modern. Die Broschüre sollte DIN A 4 - Format sein in der gewohnten Struktur Umschlagseite innen und außen und 8 - 10 Innenseiten. Im Layout sollte ein roter Faden zu erkennen sein, aber nicht jede Seite gleich aussehen. Die Anlagen sind nur beispielhaft vom bestehenden Material und sollten vom Layout keinesfalls eine Orientierung geben, denn das soll verändert werden. Die Anlagen sind für einen inhaltlichen Überblick.

```html
<!DOCTYPE html>
<html lang="de">
<head>
<meta charset="utf-8">
<title>Broschüre Chemiefreie Kühlwasseraufbereitung – Innenseiten</title>
<link href="https://fonts.googleapis.com/css2?family=Archivo:wght@400;500&family=Arimo:wght@700&family=Lato:wght@300;400;700&display=swap" rel="stylesheet">
<style>
  :root {
    --backdrop: #dcdcda;
    --paper: #f8f8f5;
    --navy: #14143f;
    --aqua: #4cbcd4;
    --frame: #d8d4cc;
    --ink: #2a2a2a;
    --number: #555559;
    --rule: #9a9a9a;
    --folio: #6a6a6a;
  }
  * { margin: 0; padding: 0; box-sizing: border-box; }
  html, body { width: 1200px; height: 900px; overflow: hidden; }
  body { background: var(--backdrop); position: relative; font-family: "Lato", sans-serif; }

  .page { position: absolute; top: 147px; width: 390px; height: 606px; overflow: hidden; }
  .page--left { left: 210px; }
  .page--right { left: 600px; background: var(--paper); }

  .photo {
    position: absolute; inset: 0;
    background:
      linear-gradient(180deg, rgba(30,30,30,.35) 0%, rgba(0,0,0,0) 30%, rgba(0,0,0,0) 60%, rgba(30,30,30,.45) 100%),
      linear-gradient(100deg, #4e4e4c 0%, #6a6a67 25%, #8a8a86 50%, #6c6c69 75%, #4a4a48 100%);
  }
  .quote-frame {
    position: absolute; left: 70px; top: 174px; width: 244px; height: 266px;
    border: 2px solid var(--frame);
  }
  .quote {
    position: absolute; right: 10px; top: 28px; width: 220px;
    font-family: "Archivo", sans-serif; font-weight: 500;
    font-size: 16px; line-height: 21px; letter-spacing: 1.4px;
    text-transform: uppercase; text-align: right; color: var(--aqua);
  }

  .band { position: absolute; left: 0; top: 0; width: 100%; height: 218px; background: var(--navy); }
  .infotext {
    position: absolute; left: 30px; top: 52px; width: 228px;
    font-family: "Arimo", sans-serif; font-weight: 700;
    font-size: 7.2px; line-height: 10px; color: #fff;
  }
  .infotext__label { color: var(--aqua); font-size: 10px; }
  .band__rule { position: absolute; left: 30px; top: 105px; width: 222px; height: 3px; background: #fff; }

  .column { position: absolute; top: 232px; width: 106px; }
  .column--1 { left: 30px; }
  .column--2 { left: 151px; }
  .column--3 { left: 272px; }
  .column__number { font-weight: 300; font-size: 26px; line-height: 30px; color: var(--number); }
  .column__title { margin-top: 28px; font-weight: 700; font-size: 10.5px; color: var(--aqua); }
  .column__text { margin-top: 9px; font-size: 5.4px; line-height: 9.6px; color: var(--ink); }
  .column__text + .column__text { margin-top: 8px; }

  .footer__rule { position: absolute; left: 30px; right: 28px; top: 586px; height: 1px; background: var(--rule); }
  .footer__folio { position: absolute; right: 30px; top: 589px; font-size: 6.5px; font-weight: 300; color: var(--folio); }
</style>
</head>
<body>
  <section class="page page--left">
    <div class="photo" role="img" aria-label="Foto einer industriellen Kühlwasseranlage mit Rohrleitungen und Pumpen in Graustufen"></div>
    <div class="quote-frame">
      <p class="quote">Lorem ipsum elitr, sed diam nonumy eirmod tempor invidunt ut labore et dolore magna aliquyam erat, sed diam voluptua. At</p>
    </div>
  </section>

  <section class="page page--right">
    <div class="band">
      <p class="infotext"><span class="infotext__label">Infotext</span> Miliquibus perem acita sum, cus.occaeped maximusa conemporunt quas est, con pro te.Nossimuscient laniatisim in nestius comnim fugia quate dolor simos delectis.Beatis is porrum et ut es etur? Ovit rate et, sum et inisquu ntionet</p>
      <div class="band__rule"></div>
    </div>

    <article class="column column--1">
      <div class="column__number">01</div>
      <h3 class="column__title">Titel 1</h3>
      <p class="column__text">Agnit erum hil eventiant.</p>
      <p class="column__text">Maiorest quia dia volesti oreedipsunte volupta non et hitatqu idella suntia voluptam ius nonecaborro doloritam non aut quanto cus dolupta testio tectas autenest, nobisseque rerum iunt rem nonsedignat.</p>
      <p class="column__text">Dolor simod es non come por a verum comnis sernatio veroid quae quaecea tum facersp elliquis sitium sinci tempe reria delam volupta tempore tempe reria dellam, volecti ssusam dem sit ipic totatqui sint quoditatur? Daesequam sandi odis magnatatus pero volorrum voluptae et alisui sum delloreicid modipide et omnolorion consedi seque volupta turibuscidem hit omniatum il is maio qual.</p>
    </article>

    <article class="column column--2">
      <div class="column__number">02</div>
      <h3 class="column__title">Titel 2</h3>
      <p class="column__text">Agnit erum hil eventiant.</p>
      <p class="column__text">Maiorest quia dia volesti oreedipsunte volupta non et hitatqu idella suntia voluptam ius nonecaborro doloritam non aut quanto cus dolupta testio tectas autenest, nobisseque rerum iunt rem nonsedignat.</p>
      <p class="column__text">Dolor simod es non come por a verum comnis sernatio veroid quae quaecea tum facersp elliquis sitium sinci tempe reria delam volupta tempore tempe reria dellam, volecti ssusam dem sit ipic totatqui sint quoditatur? Daesequam sandi odis magnatatus pero volorrum voluptae et alisui sum delloreicid modipide et omnolorion consedi seque volupta turibuscidem hit omniatum il is maio qual.</p>
    </article>

    <article class="column column--3">
      <div class="column__number">03</div>
      <h3 class="column__title">Titel 3</h3>
      <p class="column__text">tempe reria dellam, volecti ssusam dem sit ipic totatqui sint quoditatur? Daesequam sandi odis magnatatus pero volorrum voluptae et alisui sum delloreicid modipide et omnolorion consedi seque volupta turibuscidem hit omniatum il is maio qual.</p>
    </article>

    <div class="footer__rule"></div>
    <div class="footer__folio">Chemiefreie 7</div>
  </section>
</body>
</html>
```